Small Business Broker Business Card Design

A business card design for a small business brokerage, which is a financial service, not unlike real estate brokerage, but for small businesses such as laundromats, pizza shops, restaurants, cleaners etc. The designs should all be simple, more conservative in nature, using the colors and font of the logo. Again, think real estate Brokerage as a business context
Contact Information for Business Card
Name: Glen R. Harlow. Title: Small Business Advisor. Email: g.harlow@bayfieldcapitalworks.example. Mobile: (555) 274-3918. Office: (555) 806-2147. www.bayfieldcapitalworks.example

```html
<!DOCTYPE html>
<html lang="en">
<head>
<meta charset="utf-8">
<title>Bayfield Capital Works – Business Card</title>
<link href="https://fonts.googleapis.com/css2?family=Montserrat:wght@400;500;600;700&family=Libre+Baskerville:wght@700&display=swap" rel="stylesheet">
<style>
  :root {
    --stage: #2b2b2d;
    --navy: #1d2f5c;
    --green: #8cc11f;
    --paper: #ffffff;
    --ink: #2a2d36;
    --rule: #1d2f5c;
  }
  * { box-sizing: border-box; margin: 0; padding: 0; }
  html, body {
    width: 1200px; height: 688px; overflow: hidden;
    background: var(--stage);
  }
  .stage {
    width: 1200px; height: 688px;
    display: flex; align-items: center; justify-content: center; gap: 40px;
  }
  .card {
    width: 540px; height: 309px; position: relative;
    box-shadow: 0 10px 30px rgba(0,0,0,.45);
  }
  /* Front */
  .card--front {
    background: var(--navy);
    display: flex; flex-direction: column; align-items: center; justify-content: center;
  }
  .brand {
    display: flex; align-items: center; gap: 10px;
    font-family: "Montserrat", sans-serif; font-weight: 700;
    text-transform: uppercase; letter-spacing: .04em;
    white-space: nowrap;
  }
  .brand__square { width: 18px; height: 18px; flex: none; }
  .card--front .brand { color: var(--paper); font-size: 21px; }
  .card--front .brand__square { background: var(--green); }
  .tagline {
    font-family: "Montserrat", sans-serif; font-weight: 600;
    text-transform: uppercase; letter-spacing: .06em;
    color: var(--green); white-space: nowrap;
  }
  .card--front .tagline { font-size: 10.5px; margin-top: 6px; }

  /* Back */
  .card--back { background: var(--paper); }
  .contact {
    position: absolute; left: 200px; top: 34px;
    padding-left: 22px; border-left: 1.5px solid var(--rule);
    color: var(--ink);
  }
  .contact__name {
    font-family: "Libre Baskerville", serif; font-weight: 700;
    font-size: 19px; color: var(--navy);
  }
  .contact__title {
    font-family: "Montserrat", sans-serif; font-size: 11.5px; margin: 2px 0 12px;
  }
  .contact__list { list-style: none; }
  .contact__item {
    font-family: "Montserrat", sans-serif; font-size: 11.5px; line-height: 1.75;
    display: flex; gap: 8px; white-space: nowrap;
  }
  .contact__label {
    font-family: "Libre Baskerville", serif; font-weight: 700;
    color: var(--navy); width: 18px; flex: none;
  }
  .card--back .identity { position: absolute; left: 34px; bottom: 40px; }
  .card--back .brand { color: var(--navy); font-size: 23px; }
  .card--back .brand__square { background: var(--navy); }
  .card--back .tagline { font-size: 11.5px; margin-top: 4px; }
</style>
</head>
<body>
<main class="stage">
  <section class="card card--front" aria-label="Card front">
    <div class="brand"><span class="brand__square"></span>Bayfield Capital Works, Inc</div>
    <p class="tagline">Trusted guidance to buy or sell your business</p>
  </section>

  <section class="card card--back" aria-label="Card back">
    <div class="contact">
      <h1 class="contact__name">Glen R. Harlow</h1>
      <p class="contact__title">Small Business Advisor</p>
      <ul class="contact__list">
        <li class="contact__item"><span class="contact__label">M:</span>(555) 274-3918</li>
        <li class="contact__item"><span class="contact__label">O:</span>(555) 806-2147</li>
        <li class="contact__item"><span class="contact__label">E:</span>g.harlow@bayfieldcapitalworks.example</li>
        <li class="contact__item"><span class="contact__label">W:</span>www.bayfieldcapitalworks.example</li>
      </ul>
    </div>
    <div class="identity">
      <div class="brand"><span class="brand__square"></span>Bayfield Capital Works, Inc</div>
      <p class="tagline">Trusted guidance to buy or sell your business</p>
    </div>
  </section>
</main>
</body>
</html>
```